Road Construction Company needs business cards

We would like a new business card designed for our business.

We're a road construction company based in Qld, Australia.

Can the business card please have the following information on it.

Name: Warren Halbeck
Position: General Manager
Phone: 0472 915 348
Email: Warren.halbeck@tovrin.com.au
Address: 87 Marrow Ave, Pendlebay, QLD, 4023
Website: www.tovrin.com.au

Visually we'd like the card to be professional and simple.

Attached is our logo.

Our website is www.tovrin.com.au

Target Market(s)

Men aged 25-60

Contact Information for Business Card

As listed in project description

Font styles to use
Serif

Requirements
Must have
• Large logo on back of card

```html
<!DOCTYPE html>
<html lang="en">
<head>
<meta charset="utf-8">
<title>Tovrin Road Construction – Business Card</title>
<link rel="stylesheet" href="https://fonts.googleapis.com/css2?family=Open+Sans:wght@400;600;700&display=swap">
<style>
  :root {
    --backdrop: #2a2a2d;
    --card: #000000;
    --brand-blue: #1a5cb0;
    --sky-blue: #45a9dd;
    --ink-white: #ffffff;
  }
  * { margin: 0; padding: 0; box-sizing: border-box; }
  html, body { width: 1200px; height: 780px; overflow: hidden; }
  body {
    background: var(--backdrop);
    font-family: "Open Sans", Arial, sans-serif;
    position: relative;
  }
  .card {
    position: absolute;
    top: 235px;
    width: 540px;
    height: 310px;
    background: var(--card);
    border-radius: 22px;
    border: 3px solid var(--sky-blue);
    overflow: hidden;
    box-shadow: 0 18px 40px rgba(0,0,0,0.55);
  }
  .card--front { left: 40px; }
  .card--back { left: 620px; }

  .brand-name {
    color: var(--brand-blue);
    font-weight: 700;
    text-transform: uppercase;
    line-height: 1;
    letter-spacing: 0.02em;
  }
  .card--front .brand-name {
    position: absolute;
    left: 0; right: 0; top: 110px;
    text-align: center;
    font-size: 64px;
  }
  .card--front .brand-name .brand-sub {
    display: block;
    font-size: 18px;
    letter-spacing: 0.42em;
    margin-top: 10px;
  }
  .card--back .brand-name {
    position: absolute;
    left: 22px; top: 128px;
    width: 250px;
    text-align: center;
    font-size: 40px;
  }
  .card--back .brand-name .brand-sub {
    display: block;
    font-size: 11px;
    letter-spacing: 0.38em;
    margin-top: 7px;
  }

  .divider {
    position: absolute;
    left: 288px; top: 52px;
    width: 2px; height: 178px;
    background: var(--ink-white);
  }
  .contact {
    position: absolute;
    left: 310px; top: 56px;
    color: var(--ink-white);
  }
  .contact__name {
    color: var(--brand-blue);
    font-size: 22px;
    font-weight: 700;
    line-height: 1.1;
  }
  .contact__role { font-size: 13px; font-weight: 600; margin-top: 3px; }
  .contact__address { font-size: 12px; line-height: 1.45; margin-top: 12px; }
  .contact__list { list-style: none; margin-top: 12px; font-size: 12px; line-height: 1.55; }
  .contact__list li { display: flex; align-items: center; gap: 7px; }
  .contact__icon { width: 12px; height: 12px; flex: none; }

  .band { position: absolute; left: 0; bottom: 0; width: 540px; height: 60px; }
</style>
</head>
<body>

<section class="card card--front" aria-label="Card front">
  <div class="brand-name">Tovrin<span class="brand-sub">Road Construction</span></div>
</section>

<section class="card card--back" aria-label="Card back">
  <div class="brand-name">Tovrin<span class="brand-sub">Road Construction</span></div>
  <div class="divider"></div>
  <div class="contact">
    <h1 class="contact__name">Warren Halbeck</h1>
    <p class="contact__role">General Manager</p>
    <p class="contact__address">87 Marrow Ave,<br>Pendlebay, QLD, 4023</p>
    <ul class="contact__list">
      <li>
        <svg class="contact__icon" viewBox="0 0 12 12" aria-hidden="true"><circle cx="6" cy="6" r="6" fill="#45a9dd"/><path d="M3.6 3.2l1.2-.2.6 1.5-.7.5a4 4 0 0 0 1.6 1.6l.5-.7 1.5.6-.2 1.2C6 7.9 4 6 3.6 3.2z" fill="#000"/></svg>
        0472 915 348
      </li>
      <li>
        <svg class="contact__icon" viewBox="0 0 12 12" aria-hidden="true"><circle cx="6" cy="6" r="6" fill="#45a9dd"/><circle cx="6" cy="6" r="3.4" fill="none" stroke="#000" stroke-width="0.9"/><path d="M2.6 6h6.8M6 2.6c-1.6 2-1.6 4.8 0 6.8M6 2.6c1.6 2 1.6 4.8 0 6.8" fill="none" stroke="#000" stroke-width="0.8"/></svg>
        www.tovrin.com.au
      </li>
      <li>
        <svg class="contact__icon" viewBox="0 0 12 12" aria-hidden="true"><circle cx="6" cy="6" r="6" fill="#45a9dd"/><rect x="3" y="3.8" width="6" height="4.4" fill="none" stroke="#000" stroke-width="0.9"/><path d="M3 3.8l3 2.5 3-2.5" fill="none" stroke="#000" stroke-width="0.9"/></svg>
        Warren.halbeck@tovrin.com.au
      </li>
    </ul>
  </div>
  <svg class="band" viewBox="0 0 540 60" aria-hidden="true">
    <rect x="0" y="40" width="340" height="14" fill="#45a9dd"/>
    <rect x="350" y="30" width="190" height="10" fill="#1a5cb0"/>
  </svg>
</section>

</body>
</html>
```